New Zealand Marlborough Sauvignon Blanc wine packaging design

We need packaging design for our new wine brand, Dunmore Vale. The wine is a New Zealand Marlborough Sauvignon Blanc. We would like the packaging will portray elegance and style with an understated label. We are looking for a label that portrays the elegance of the French Riviera. The label should be round or pill shaped.
Updates

Industry/Entity Type

Wine

Font styles to use
Serif
Sans Serif

Requirements
Must have
• The words in order of importance: Dunmore Vale, Sauvignon Blanc, Marlborough, New Zealand. It should be fit to the bottle posted in the links
Nice to have
• a pill shape or circular shape
Should not have
• Illustrations of wine bottles, wine glasses, or grapes

```html
<!DOCTYPE html>
<html lang="en">
<head>
<meta charset="UTF-8">
<title>Dunmore Vale – Wine Label</title>
<link href="https://fonts.googleapis.com/css2?family=Allura&family=Open+Sans:wght@400;600&display=swap" rel="stylesheet">
<style>
  :root {
    --backdrop: #e9e8e6;
    --label-black: #1c1c1d;
    --ring-black: #141414;
    --ring-gap: #ffffff;
    --gold: #a78f52;
    --gold-deep: #7d6a3a;
    --gold-light: #c9b27a;
  }
  html, body {
    margin: 0;
    padding: 0;
    overflow: hidden;
  }
  body {
    width: 1200px;
    height: 1180px;
    background: var(--backdrop);
  }
  .canvas {
    position: relative;
    width: 1200px;
    height: 1180px;
    overflow: hidden;
  }
  .label-shape {
    position: absolute;
    inset: 0;
  }
  .brand-name {
    position: absolute;
    left: 0;
    right: 0;
    top: 540px;
    margin: 0;
    text-align: center;
    font-family: "Allura", cursive;
    font-weight: 400;
    font-size: 128px;
    line-height: 1;
    color: var(--gold);
  }
  .region {
    position: absolute;
    left: 0;
    right: 0;
    top: 710px;
    margin: 0;
    text-align: center;
    font-family: "Open Sans", sans-serif;
    font-weight: 600;
    font-size: 25px;
    letter-spacing: 0.22em;
    color: var(--gold);
  }
  .volume {
    position: absolute;
    left: 0;
    right: 0;
    top: 955px;
    margin: 0;
    text-align: center;
    font-family: "Open Sans", sans-serif;
    font-weight: 400;
    font-size: 38px;
    color: var(--gold);
  }
</style>
</head>
<body>
<main class="canvas">
  <svg class="label-shape" width="1200" height="1180" viewBox="0 0 1200 1180">
    <defs>
      <clipPath id="label-face">
        <ellipse cx="600" cy="590" rx="432" ry="508"/>
      </clipPath>
      <linearGradient id="vineyard-tones" x1="0" y1="0" x2="0" y2="1">
        <stop offset="0" stop-color="#1c1c1d"/>
        <stop offset="0.35" stop-color="#3a3426"/>
        <stop offset="0.7" stop-color="#6e5f38"/>
        <stop offset="1" stop-color="#2a2720"/>
      </linearGradient>
    </defs>
    <ellipse class="outer-ring" cx="600" cy="590" rx="470" ry="528" fill="var(--ring-gap)" stroke="var(--ring-black)" stroke-width="12"/>
    <ellipse class="label-face" cx="600" cy="590" rx="432" ry="508" fill="var(--label-black)"/>
    <g clip-path="url(#label-face)">
      <rect class="vineyard-scene" x="150" y="160" width="900" height="400" fill="url(#vineyard-tones)" role="img" aria-label="Engraved gold line illustration of a vineyard landscape with rolling vine rows, farmhouses, hills and clouds"/>
    </g>
  </svg>
  <h1 class="brand-name">Dunmore Vale</h1>
  <p class="region">MARLBOROUGH, NEW ZEALAND</p>
  <p class="volume">750ml</p>
</main>
</body>
</html>
```